Pawn & Gun store business card design

Hello! We would like a new business card design for our pawn & gun store. We loan money on items of value and sell firearms, jewelry, electronics & more.

Card will need to have the following information:

Business name - Prairie Nickel Pawn & Gun
Address - 2417 Hwy 53 S. Suite C Wylie, TX 75246
Employees name - Darren Kellum
Phone number - 972-613-8840
Email - PrairieNickelPawn@Mailvera.com
Website - PrairieNickelPawn.com

Somewhere on the card we would like it to say "Offering 10 Month Layaway!" & "We buy & loan on anything of value!". Our main store color is orange (please see logo). Logo does not have to be on the business card but it can be. Would like the back to have an area to write a note on the back. We like vintage things like old coins, collectables, firearms and more so think about this in the design. We want a business card as unique as our store!

Colors

Designer to choose colors to be used in the design.

Requirements
Nice to have
• Vintage Style

```html
<!DOCTYPE html>
<html lang="en">
<head>
<meta charset="utf-8">
<title>Prairie Nickel Pawn &amp; Gun – Business Card</title>
<link href="https://fonts.googleapis.com/css2?family=Arvo:wght@700&family=Roboto:wght@400&family=EB+Garamond:wght@400;700&display=swap" rel="stylesheet">
<style>
  :root {
    --page: #efece6;
    --kraft: #c1a27c;
    --kraft-edge: #a88a66;
    --orange: #c2461a;
    --ink: #3e2e22;
    --text: #4a3c30;
    --rule: #5a4736;
    --ghost: rgba(120, 90, 60, 0.13);
  }
  * { margin: 0; padding: 0; box-sizing: border-box; }
  html, body { width: 1200px; height: 800px; overflow: hidden; background: var(--page); }
  .canvas { position: relative; width: 1200px; height: 800px; }
  .card {
    position: absolute; left: 330px; width: 540px; height: 316px;
    background: var(--kraft);
    box-shadow: 0 2px 0 var(--kraft-edge), 0 4px 10px rgba(0,0,0,0.12);
  }
  .card--front { top: 52px; }
  .card--back { top: 432px; }

  /* Front */
  .brand {
    position: absolute; left: 52px; top: 112px; width: 190px;
    display: flex; flex-direction: column; align-items: center; gap: 8px;
  }
  .brand__dot { width: 16px; height: 16px; border-radius: 50%; background: var(--orange); }
  .brand__name {
    font-family: 'Arvo', serif; font-weight: 700; font-size: 22px; line-height: 1.1;
    color: var(--orange); text-align: center; text-transform: uppercase;
  }
  .divider {
    position: absolute; left: 257px; top: 84px; width: 1px; height: 140px; background: var(--rule); opacity: .7;
  }
  .contact { position: absolute; left: 278px; top: 82px; font-family: 'Roboto', sans-serif; color: var(--text); }
  .contact__name {
    font-family: 'Arvo', serif; font-weight: 700; font-size: 18px; color: var(--orange);
    text-transform: uppercase; margin-bottom: 12px; letter-spacing: .2px;
  }
  .contact__company { font-size: 13px; margin-bottom: 6px; }
  .contact__address { font-size: 12px; line-height: 1.25; margin-bottom: 12px; }
  .contact__list { list-style: none; font-size: 12px; }
  .contact__list li { display: flex; align-items: center; gap: 9px; height: 17px; }
  .contact__list svg { width: 11px; height: 11px; fill: var(--orange); flex: none; }

  /* Back */
  .ghost-name {
    position: absolute; left: 0; right: 0; top: 105px; text-align: center;
    font-family: 'Arvo', serif; font-weight: 700; font-size: 48px; line-height: 1.05;
    color: var(--ghost); text-transform: uppercase;
  }
  .note-line { position: absolute; left: 18px; right: 18px; height: 1px; background: var(--rule); }
  .offer {
    position: absolute; left: 0; right: 0; top: 250px; text-align: center;
    font-family: 'EB Garamond', serif; font-weight: 700; font-size: 20px; color: var(--ink); letter-spacing: .3px;
  }
  .tagline {
    position: absolute; left: 0; right: 0; top: 276px;
    display: flex; justify-content: center; align-items: center; gap: 4px;
    font-family: 'EB Garamond', serif; font-size: 15px; color: var(--orange);
  }
  .tagline::before, .tagline::after { content: ""; width: 38px; height: 1px; background: var(--ink); }
</style>
</head>
<body>
<main class="canvas">
  <section class="card card--front" aria-label="Card front">
    <div class="brand">
      <span class="brand__dot"></span>
      <span class="brand__name">Prairie Nickel<br>Pawn</span>
    </div>
    <div class="divider"></div>
    <div class="contact">
      <p class="contact__name">Darren Kellum</p>
      <p class="contact__company">Prairie Nickel Pawn &amp; Gun</p>
      <p class="contact__address">2417 Hwy 53 S.<br>Suite C Wylie, TX 75246</p>
      <ul class="contact__list">
        <li><svg viewBox="0 0 24 24"><path d="M6.6 10.8a15.1 15.1 0 0 0 6.6 6.6l2.2-2.2a1 1 0 0 1 1-.25 11.4 11.4 0 0 0 3.6.57 1 1 0 0 1 1 1V20a1 1 0 0 1-1 1A17 17 0 0 1 3 4a1 1 0 0 1 1-1h3.5a1 1 0 0 1 1 1c0 1.25.2 2.45.57 3.57a1 1 0 0 1-.25 1z"/></svg>972-613-8840</li>
        <li><svg viewBox="0 0 24 24"><path d="M2 5h20v14H2z M2 5l10 8 10-8" stroke="#c1a27c" stroke-width="1.5"/></svg>PrairieNickelPawn@Mailvera.com</li>
        <li><svg viewBox="0 0 24 24"><circle cx="12" cy="12" r="10"/><path d="M2 12h20M12 2c3 3 3 17 0 20M12 2c-3 3-3 17 0 20" stroke="#c1a27c" stroke-width="1.5" fill="none"/></svg>www.PrairieNickelPawn.com</li>
      </ul>
    </div>
  </section>

  <section class="card card--back" aria-label="Card back with note lines">
    <p class="ghost-name">Prairie Nickel<br>Pawn</p>
    <div class="note-line" style="top:45px"></div>
    <div class="note-line" style="top:98px"></div>
    <div class="note-line" style="top:137px"></div>
    <div class="note-line" style="top:183px"></div>
    <div class="note-line" style="top:236px"></div>
    <p class="offer">OFFERING 10 MONTH LAYAWAY</p>
    <p class="tagline">We buy &amp; loan on anything of value</p>
  </section>
</main>
</body>
</html>
```